New energy tablet requires a logo / packaging design

We need a logo designed for a new energy tablet (capsule) called "Q-Vibe". We would like to see designs that communicate a fun, youthful brand aimed primarily at a demographic of 18 - 35.

This will be a herbal energy tablet to be sold online to to people looking to increase energy and mood lifts.

We do have a previous design that we used before and would like that one to be used again but just revamped a little to give it a fresher look and more depth to the design if possible.

Completely new designs are also welcome if you would prefer but ideally we want it to look as similar to the original one as possible.

We are committed to payment on this design.

Thank you all in advance for your design submissions.

These are to be printed onto black foil zip seal bags to contain 1 pellet only.

Target Market(s)

customers that visit online and high street shops that sell herbal energy products

Industry/Entity Type

Online

Requirements
Must have
• Must have the words Q-VIBE and PELLET in the logo design

```html
<!DOCTYPE html>
<html lang="en">
<head>
<meta charset="utf-8">
<title>Q-Vibe Pellet – Energy Tablet Packaging</title>
<link href="https://fonts.googleapis.com/css2?family=Roboto+Condensed:wght@400;700&display=swap" rel="stylesheet">
<style>
  :root {
    --stage-top: #ebebeb;
    --stage-bottom: #f7f5f5;
    --pack-teal: #00a88f;
    --panel-dark: #06191a;
    --panel-mid: #0d3f3f;
    --panel-glow: #17605e;
    --frame-silver: #b9c2c3;
    --frame-shadow: #5d6768;
    --logo-aqua: #7fd8d6;
    --text-teal: #15a58f;
    --pill-dark: #1c1c1e;
    --text-white: #ffffff;
    --icon-fill: #0f8f84;
  }
  html, body {
    margin: 0;
    width: 1200px;
    height: 1000px;
    overflow: hidden;
  }
  body {
    background: linear-gradient(var(--stage-top), var(--stage-bottom));
    font-family: "Roboto Condensed", Arial, sans-serif;
  }
  .pack-label {
    position: absolute;
    left: 310px;
    top: 101px;
    width: 580px;
    height: 798px;
    box-shadow: 0 6px 18px rgba(0,0,0,0.18);
  }
  .pack-label text { font-family: "Roboto Condensed", Arial, sans-serif; }
  .brand-name { fill: var(--logo-aqua); font-weight: 700; font-size: 84px; letter-spacing: 1px; }
  .product-form { fill: var(--logo-aqua); font-weight: 700; font-size: 22px; letter-spacing: 1px; }
  .supplement-line { fill: var(--text-teal); font-weight: 700; font-size: 17px; letter-spacing: 0.5px; }
  .product-type { fill: var(--text-white); font-weight: 700; font-size: 25px; letter-spacing: 0.5px; }
  .count-line { fill: var(--text-white); font-weight: 700; font-size: 16px; letter-spacing: 0.3px; }
  .benefit-caption { fill: #d8e6e5; font-weight: 700; font-size: 9.5px; }
</style>
</head>
<body>
  <svg class="pack-label" viewBox="0 0 545 750" role="group" aria-label="Q-Vibe Pellet energy tablet front label">
    <defs>
      <linearGradient id="panelShade" x1="0" y1="0" x2="0" y2="1">
        <stop offset="0" stop-color="var(--panel-dark)"/>
        <stop offset="0.35" stop-color="var(--panel-mid)"/>
        <stop offset="0.7" stop-color="var(--panel-glow)"/>
        <stop offset="1" stop-color="var(--panel-dark)"/>
      </linearGradient>
      <linearGradient id="lowerShade" x1="0" y1="0" x2="0" y2="1">
        <stop offset="0" stop-color="var(--panel-dark)"/>
        <stop offset="0.5" stop-color="var(--panel-glow)"/>
        <stop offset="1" stop-color="var(--panel-dark)"/>
      </linearGradient>
      <linearGradient id="silverEdge" x1="0" y1="0" x2="1" y2="1">
        <stop offset="0" stop-color="var(--frame-silver)"/>
        <stop offset="0.5" stop-color="var(--frame-shadow)"/>
        <stop offset="1" stop-color="var(--frame-silver)"/>
      </linearGradient>
      <radialGradient id="iconBadge" cx="0.5" cy="0.4" r="0.6">
        <stop offset="0" stop-color="#2bb8a8"/>
        <stop offset="1" stop-color="var(--icon-fill)"/>
      </radialGradient>
    </defs>

    <rect class="pack-base" width="545" height="750" fill="var(--pack-teal)"/>

    <polygon class="top-panel" points="80,0 465,0 465,430 422,472 123,472 80,430"
             fill="url(#panelShade)" stroke="url(#silverEdge)" stroke-width="6"/>

    <text class="brand-name" x="272" y="352" text-anchor="middle">Q-VIBE</text>
    <text class="product-form" x="272" y="390" text-anchor="middle">PELLET</text>

    <text class="supplement-line" x="272" y="452" text-anchor="middle">DIETARY SUPPLEMENT</text>

    <rect class="type-pill" x="118" y="487" width="309" height="40" rx="20" fill="var(--pill-dark)"/>
    <text class="product-type" x="272" y="516" text-anchor="middle">ENERGY TABLET</text>

    <polygon class="bottom-panel" points="123,545 422,545 465,580 465,750 80,750 80,580"
             fill="url(#lowerShade)" stroke="url(#silverEdge)" stroke-width="6"/>
    <text class="count-line" x="272" y="581" text-anchor="middle">120 CAPSULES VEGETARIAN</text>

    <g class="benefit-icons">
      <circle cx="155" cy="627" r="31" fill="url(#iconBadge)" stroke="var(--frame-silver)" stroke-width="4" role="img" aria-label="Herbs and mortar icon"/>
      <circle cx="232" cy="627" r="31" fill="url(#iconBadge)" stroke="var(--frame-silver)" stroke-width="4" role="img" aria-label="Head with gears icon"/>
      <circle cx="310" cy="627" r="31" fill="url(#iconBadge)" stroke="var(--frame-silver)" stroke-width="4" role="img" aria-label="DNA strand icon"/>
      <circle cx="388" cy="627" r="31" fill="url(#iconBadge)" stroke="var(--frame-silver)" stroke-width="4" role="img" aria-label="Lightning bolt icon"/>
    </g>
    <g class="benefit-captions">
      <text class="benefit-caption" x="155" y="680" text-anchor="middle">100% NATURAL</text>
      <text class="benefit-caption" x="232" y="680" text-anchor="middle">MOOD LIFTS</text>
      <text class="benefit-caption" x="310" y="680" text-anchor="middle">NON-GMO</text>
      <text class="benefit-caption" x="388" y="680" text-anchor="middle">INCREASE ENERGY</text>
    </g>
  </svg>
</body>
</html>
```